Business Card for my New Brokerage

Looking to get a business card design for my new Real Estate Brokerage.
I want it with Picture, Phone Number, Email, Website, Office Address
Name and Designation. Please add logo too.

Target Market(s)

Real Estate Investors or Home Buyers

Industry/Entity Type

Real Estate

Contact Information for Business Card

Name, Email, Phone Number, website, email, office address

Colors
EB3D1F
EC4F4E
F09395
F8D3D4
FCEDEE

Requirements
Must have
• Minimalistic, Clean, Modern, Photo
Nice to have
• White and Red Colors

```html
<!DOCTYPE html>
<html lang="en">
<head>
<meta charset="utf-8">
<title>Lumen Realty Inc — Business Card</title>
<link href="https://fonts.googleapis.com/css2?family=Montserrat:wght@400;600;700;800&display=swap" rel="stylesheet">
<style>
  :root {
    --brand-red: #d90000;
    --ink: #3a3a3a;
    --paper: #ffffff;
    --backdrop: #b0b1ad;
    --suit: #1f2536;
    --shirt: #c9dcf2;
  }
  * { box-sizing: border-box; margin: 0; padding: 0; }
  html, body { width: 1200px; height: 801px; overflow: hidden; }
  body {
    background: var(--backdrop);
    font-family: "Montserrat", sans-serif;
    display: flex;
    align-items: center;
    justify-content: center;
    gap: 36px;
  }
  .card {
    width: 540px;
    height: 309px;
    position: relative;
    overflow: hidden;
    box-shadow: 0 10px 24px rgba(0,0,0,0.18);
  }

  /* Front */
  .card--front { background: var(--paper); }
  .front__photo {
    position: absolute;
    right: 0; top: 40px;
    width: 260px; height: 269px;
    background: linear-gradient(180deg, #d8b9a2 0%, #c49a80 35%, var(--shirt) 55%, var(--suit) 75%, var(--suit) 100%);
  }
  .front__info {
    position: absolute;
    left: 34px; top: 42px;
    width: 270px;
  }
  .wordmark {
    color: var(--brand-red);
    font-weight: 800;
  }
  .wordmark__name { display: block; font-size: 34px; line-height: 1; letter-spacing: 0.5px; }
  .wordmark__sub {
    display: block;
    font-size: 10px;
    letter-spacing: 5px;
    margin-top: 4px;
    font-weight: 800;
  }
  .person {
    margin-top: 26px;
    padding-left: 14px;
    position: relative;
  }
  .person::before {
    content: "";
    position: absolute;
    left: -34px; top: 2px;
    width: 10px; height: 30px;
    background: var(--brand-red);
  }
  .person__name {
    color: var(--brand-red);
    font-weight: 700;
    font-size: 17px;
    letter-spacing: 1px;
  }
  .person__title { color: var(--ink); font-size: 12px; margin-top: 2px; }
  .address { color: var(--ink); font-size: 12px; line-height: 1.45; margin-top: 12px; padding-left: 14px; }
  .contacts { list-style: none; margin-top: 10px; padding-left: 14px; }
  .contacts li {
    display: flex; align-items: center; gap: 7px;
    color: var(--ink); font-size: 12px; line-height: 1.6;
  }
  .contacts svg { width: 10px; height: 10px; flex: none; }

  /* Back */
  .card--back {
    background: var(--brand-red);
    display: flex;
    align-items: center;
    justify-content: center;
  }
  .card--back .wordmark { color: var(--paper); }
  .card--back .wordmark__name { font-size: 78px; letter-spacing: 1px; }
  .card--back .wordmark__sub { font-size: 22px; letter-spacing: 11px; margin-top: 8px; }
</style>
</head>
<body>
  <section class="card card--front">
    <div class="front__photo" role="img" aria-label="Portrait photo of the broker in a navy blazer and light blue shirt"></div>
    <div class="front__info">
      <div class="wordmark">
        <span class="wordmark__name">LUMEN</span>
        <span class="wordmark__sub">REALTY INC</span>
      </div>
      <div class="person">
        <p class="person__name">DANIEL HARPER</p>
        <p class="person__title">Founder and President</p>
      </div>
      <p class="address">1820 Cedar Ridge Way<br>Maple Grove, GA 30210</p>
      <ul class="contacts">
        <li>
          <svg viewBox="0 0 10 10"><path d="M2 1 L4 3 L3 4 Q4 6 6 7 L7 6 L9 8 L8 9 Q3 9 1 2 Z" fill="#d90000"/></svg>
          +330 555-0142
        </li>
        <li>
          <svg viewBox="0 0 10 10"><rect x="0.7" y="2" width="8.6" height="6" fill="none" stroke="#d90000" stroke-width="1.2"/><path d="M1 2.5 L5 5.5 L9 2.5" fill="none" stroke="#d90000" stroke-width="1.2"/></svg>
          hello@lumenrealtyinc.com
        </li>
        <li>
          <svg viewBox="0 0 10 10"><circle cx="5" cy="5" r="4.3" fill="none" stroke="#d90000" stroke-width="1.2"/><path d="M0.7 5 H9.3 M5 0.7 V9.3" stroke="#d90000" stroke-width="1"/></svg>
          www.lumenrealtyinc.com
        </li>
      </ul>
    </div>
  </section>

  <section class="card card--back">
    <div class="wordmark">
      <span class="wordmark__name">LUMEN</span>
      <span class="wordmark__sub">REALTY INC</span>
    </div>
  </section>
</body>
</html>
```